Our company needs a Corporate Identity Package!!!

We would like to receive submissions for a corporate identity pachage including the following elements:

1. Presentation Folder
2. Product/Service Catalogue (16 A4 pages landscape but expandable)
3. Product Brochure (up to 8 A4 pages)
4. Product Flyer (2 A4 pages)
5. Business Card
6. Letterhead
7. Envelope
8. E-mail signature.

I attach a Presentation Folder that i like (geometric but also has circle). We would like to have some ideas regarding the above 7 elements including brindavex logo colors (brindavex.net).

Payment is indicative and we are planning to increase the payment now that we found out how to actually do this. You are also more than welcome to send us a message and suggest the amount of payment for your Corporate Identity elements and we will update this.

Target Market(s)

Home | Office | Life

Colors
f78f20
0555a3
9bcb3b

Requirements
Must have
• 1. Presentation Folder
• 2. Product/Service Catalogue (16 A4 pages landscape but to be easily expandable)
• 3. Product Brochure (up to 4 A4 pages but to be easily expandable )
• 4. Product Flyer (2 A4 pages)
• 5. Business Card
• 6. Letterhead
• 7. Envelope
• 8. E-mail signature.
Nice to have
• It would be nice to include design something around the cycle that communicates the best six doctors (i.e. sunshine, water, rest, air, exercise and diet) !!!

```html
<!DOCTYPE html>
<html lang="en">
<head>
<meta charset="utf-8">
<title>brindavex – Product Flyer</title>
<link href="https://fonts.googleapis.com/css2?family=Open+Sans:wght@400;600;700;800&display=swap" rel="stylesheet">
<style>
  :root {
    --stage: #1c1c1e;
    --paper: #ffffff;
    --navy: #262a6b;
    --orange: #f78f20;
    --blue: #0555a3;
    --green: #9bcb3b;
    --ink: #333333;
    --muted: #6b6b6b;
  }
  * { margin: 0; padding: 0; box-sizing: border-box; }
  html, body { width: 1200px; height: 713px; overflow: hidden; }
  body {
    background: var(--stage);
    font-family: "Open Sans", Arial, sans-serif;
    color: var(--ink);
    position: relative;
  }
  .page {
    position: absolute;
    top: 36px;
    width: 452px;
    height: 640px;
    background: var(--paper);
    overflow: hidden;
  }
  .page--cover { left: 130px; }
  .page--products { left: 618px; }
  .page__art { position: absolute; inset: 0; width: 100%; height: 100%; }

  /* cover */
  .brand {
    position: absolute;
    left: 44px;
    top: 118px;
    display: flex;
    align-items: center;
    gap: 10px;
  }
  .brand__dot { width: 30px; height: 30px; border-radius: 50%; background: var(--green); }
  .brand__name {
    font-size: 38px;
    font-weight: 600;
    color: #ffffff;
    letter-spacing: -0.5px;
    line-height: 1;
  }
  .brand__tagline {
    position: absolute;
    left: 86px;
    top: 164px;
    font-size: 8px;
    letter-spacing: 3px;
    color: #c9cbe8;
  }
  .contact {
    position: absolute;
    left: 16px;
    right: 16px;
    bottom: 14px;
    display: flex;
    justify-content: space-between;
    font-size: 9px;
    color: var(--muted);
  }
  .contact__item { display: flex; align-items: center; gap: 5px; }
  .contact__icon {
    width: 12px; height: 12px; border-radius: 50%;
    background: var(--orange);
    display: inline-flex; align-items: center; justify-content: center;
  }

  /* products */
  .products__title {
    position: absolute;
    left: 38px;
    top: 66px;
    font-size: 22px;
    font-weight: 800;
    color: var(--navy);
  }
  .products__intro {
    position: absolute;
    left: 38px;
    top: 100px;
    width: 300px;
    font-size: 8px;
    line-height: 1.45;
    color: var(--ink);
  }
  .products__intro p + p { margin-top: 6px; }
  .product-row {
    position: absolute;
    left: 30px;
    top: 200px;
    width: 392px;
    display: flex;
    justify-content: space-between;
  }
  .product { width: 118px; text-align: left; }
  .product__frame { display: block; width: 100px; height: 88px; margin: 0 auto 14px; }
  .product__name { font-size: 12px; font-weight: 700; color: var(--green); }
  .product__text { font-size: 7.5px; line-height: 1.4; color: var(--muted); margin-top: 3px; width: 100px; }
  .products__closing {
    position: absolute;
    left: 196px;
    top: 412px;
    width: 236px;
    font-size: 8px;
    line-height: 1.5;
    color: var(--ink);
  }
</style>
</head>
<body>

  <section class="page page--cover" aria-label="Flyer cover">
    <svg class="page__art" viewBox="0 0 452 640" aria-hidden="true">
      <defs>
        <linearGradient id="orangeDisc" x1="0" y1="0" x2="1" y2="1">
          <stop offset="0" stop-color="#f9a13a"/>
          <stop offset="1" stop-color="#f07e12"/>
        </linearGradient>
        <linearGradient id="coverMosaic" x1="0" y1="0" x2="1" y2="1">
          <stop offset="0" stop-color="#9bcb3b"/>
          <stop offset="0.45" stop-color="#f78f20"/>
          <stop offset="0.75" stop-color="#e8e04a"/>
          <stop offset="1" stop-color="#0555a3"/>
        </linearGradient>
      </defs>
      <rect x="0" y="0" width="452" height="220" fill="var(--navy)"/>
      <circle cx="230" cy="130" r="240" fill="var(--navy)"/>
      <circle cx="320" cy="340" r="170" fill="url(#orangeDisc)"/>
      <polygon points="0,215 330,300 0,440" fill="var(--green)"/>
      <line x1="70" y1="262" x2="440" y2="340" stroke="var(--orange)" stroke-width="1.5"/>
      <line x1="180" y1="292" x2="300" y2="300" stroke="#3a3f8a" stroke-width="1.5"/>
      <polygon points="30,360 180,300 330,390 300,480 170,520 60,470" fill="url(#coverMosaic)" opacity="0.9"/>
      <polygon points="0,470 150,520 100,600 0,590" fill="url(#coverMosaic)" opacity="0.55"/>
      <circle cx="360" cy="470" r="58" fill="var(--blue)"/>
    </svg>
    <div role="img" aria-label="Geometric triangle mosaic in green, orange, yellow and blue" style="position:absolute;left:30px;top:300px;width:300px;height:220px;"></div>

    <div class="brand">
      <span class="brand__dot"></span>
      <span class="brand__name">brindavex</span>
    </div>
    <div class="brand__tagline">HOME &nbsp;OFFICE &nbsp;LIFE</div>

    <footer class="contact">
      <span class="contact__item">
        <span class="contact__icon"><svg width="7" height="7" viewBox="0 0 10 10"><path d="M2 1 L4 1 L5 3 L4 4 Q5 6 6 6 L7 5 L9 6 L9 8 Q5 9 2 5 Q1 3 2 1Z" fill="#fff"/></svg></span>
        +1 555 014 2280
      </span>
      <span class="contact__item">
        <span class="contact__icon"><svg width="7" height="7" viewBox="0 0 10 10"><rect x="1" y="2.5" width="8" height="5.5" fill="none" stroke="#fff"/><path d="M1 2.5 L5 6 L9 2.5" fill="none" stroke="#fff"/></svg></span>
        hello@brindavex.net
      </span>
      <span class="contact__item">
        <span class="contact__icon"><svg width="7" height="7" viewBox="0 0 10 10"><path d="M5 9 Q1 5 1 3.5 A4 4 0 0 1 9 3.5 Q9 5 5 9Z" fill="#fff"/></svg></span>
        24 Linden Row, Harbor City
      </span>
    </footer>
  </section>

  <section class="page page--products" aria-label="Products page">
    <svg class="page__art" viewBox="0 0 452 640" aria-hidden="true">
      <defs>
        <linearGradient id="productsMosaic" x1="0" y1="0" x2="1" y2="1">
          <stop offset="0" stop-color="#9bcb3b"/>
          <stop offset="0.4" stop-color="#e8e04a"/>
          <stop offset="0.7" stop-color="#f78f20"/>
          <stop offset="1" stop-color="#0555a3"/>
        </linearGradient>
      </defs>
      <polygon points="250,0 452,0 452,110 400,90 330,60 270,40" fill="url(#productsMosaic)" opacity="0.9"/>
      <polygon points="30,420 110,385 170,420 150,490 70,500 20,470" fill="url(#productsMosaic)" opacity="0.9"/>
    </svg>
    <div role="img" aria-label="Geometric triangle mosaic, top corner" style="position:absolute;left:250px;top:0;width:202px;height:110px;"></div>
    <div role="img" aria-label="Geometric triangle mosaic cluster" style="position:absolute;left:20px;top:385px;width:150px;height:115px;"></div>

    <h1 class="products__title">OUR PRODUCTS</h1>
    <div class="products__intro">
      <p>Our range brings clean, bright design into every room of the home and office. Each product is made from durable materials, tested for daily use, and finished with care so it looks good for years. We keep prices fair, delivery quick and support friendly, because the things around you should make life simpler, calmer and more colourful.</p>
      <p>Every item is chosen to help you rest, work and live better, with simple shapes and honest quality.</p>
    </div>

    <div class="product-row">
      <article class="product">
        <svg class="product__frame" viewBox="0 0 100 88" aria-hidden="true"><polygon points="25,2 75,2 98,44 75,86 25,86 2,44" fill="none" stroke="var(--orange)" stroke-width="2.5"/></svg>
        <h2 class="product__name">Health products</h2>
        <p class="product__text">Light, useful and built to last for daily life.</p>
      </article>
      <article class="product">
        <svg class="product__frame" viewBox="0 0 100 88" aria-hidden="true"><polygon points="25,2 75,2 98,44 75,86 25,86 2,44" fill="none" stroke="var(--orange)" stroke-width="2.5"/></svg>
        <h2 class="product__name">Health products</h2>
        <p class="product__text">Light, useful and built to last for daily life.</p>
      </article>
      <article class="product">
        <svg class="product__frame" viewBox="0 0 100 88" aria-hidden="true"><polygon points="25,2 75,2 98,44 75,86 25,86 2,44" fill="none" stroke="var(--orange)" stroke-width="2.5"/></svg>
        <h2 class="product__name">Health products</h2>
        <p class="product__text">Light, useful and built to last for daily life.</p>
      </article>
    </div>

    <p class="products__closing">We design for the way people live today. From the kitchen table to the meeting room, our products bring order, comfort and a bit of colour. Talk to our team to find the right fit for your space and budget.</p>
  </section>

</body>
</html>
```